Banner Pop Up Opt In Form REDESIGNS - SLEEK BLACK LOOK

Please redesign banners attached.

I am looking for a very sleek look....I do not like this collage of images on these current designs. Please keep all content same but use images that pop.

I have an acccount at www.pixvane-example.com or you can use your own images.

I like black background for somereason because it looks very sleek....but these designs should pop , build trust and credibility and have easy opt in form....SLEEK AND MODERN LOOK is what im looking for....

Target Market(s)

Consumers on websites

Requirements
Must have
• Please redesign banners attached.

Nice to have

Should not have

```html
<!DOCTYPE html>
<html lang="en">
<head>
<meta charset="utf-8">
<title>Restaurant Certificate Opt-In Banners</title>
<link rel="stylesheet" href="https://fonts.googleapis.com/css2?family=Playfair+Display:wght@600;700&family=Montserrat:wght@400;500;700&display=swap">
<style>
  :root {
    --page-bg: #000000;
    --accent: #f2a24d;
    --ink-dark: #2a1f17;
    --text-light: #ffffff;
    --text-muted: #d8d2cc;
    --form-panel: rgba(255,255,255,0.82);
    --label-dark: #4a423c;
  }
  * { margin: 0; padding: 0; box-sizing: border-box; }
  html, body { width: 1200px; height: 2400px; overflow: hidden; background: var(--page-bg); }
  body { position: relative; font-family: "Montserrat", sans-serif; }

  .banner { position: absolute; left: 120px; width: 960px; height: 960px; overflow: hidden; }
  .banner--offer { top: 142px; }
  .banner--win { top: 1300px; }

  .photo { position: absolute; left: 0; top: 0; width: 100%; }
  .photo--diners {
    height: 100%;
    background:
      radial-gradient(ellipse at 25% 55%, #7a4a35 0%, rgba(80,45,30,0) 45%),
      radial-gradient(ellipse at 60% 55%, #3c5f7a 0%, rgba(40,60,80,0) 35%),
      radial-gradient(ellipse at 88% 60%, #8fb2cc 0%, rgba(120,150,180,0) 30%),
      linear-gradient(180deg, #1d1915 0%, #2b231c 45%, #4a3327 75%, #6a4a38 100%);
  }
  .photo--plating {
    height: 537px;
    background:
      radial-gradient(ellipse at 55% 70%, #f1eeea 0%, #cfc9c2 25%, rgba(120,115,110,0) 50%),
      radial-gradient(ellipse at 50% 62%, #7a2a22 0%, rgba(120,40,30,0) 18%),
      radial-gradient(ellipse at 35% 25%, #a77a62 0%, rgba(160,120,100,0) 25%),
      linear-gradient(180deg, #3a3633 0%, #6d6864 45%, #5a5653 100%);
  }
  .dark-panel {
    position: absolute; left: 0; top: 537px; width: 100%; height: 423px;
    background: linear-gradient(180deg, #1f1b18 0%, #2a2522 55%, #1c1917 100%);
  }

  .headline {
    position: absolute; left: 0; width: 100%;
    font-family: "Playfair Display", serif; font-weight: 700;
    color: var(--accent); letter-spacing: -3px; line-height: 1;
  }
  .banner--offer .headline { top: 44px; text-align: center; font-size: 72px; }
  .banner--win .headline { top: 580px; left: 28px; width: auto; font-size: 70px; }

  .subline {
    position: absolute; color: var(--text-light);
    font-size: 25px; font-weight: 500; letter-spacing: 4px; line-height: 38px; text-transform: uppercase;
  }
  .banner--offer .subline { top: 122px; left: 0; width: 100%; text-align: center; }
  .banner--win .subline { top: 674px; left: 28px; }

  .ribbon { position: absolute; }
  .ribbon svg { position: absolute; left: 0; top: 0; }
  .ribbon__text {
    position: absolute; color: var(--ink-dark);
    font-weight: 700; font-size: 24px; letter-spacing: 4px; line-height: 32px; text-transform: uppercase;
  }
  .banner--offer .ribbon { left: 262px; top: 214px; width: 437px; height: 77px; }
  .banner--offer .ribbon__text { left: 0; top: 6px; width: 100%; text-align: center; }
  .banner--win .ribbon { left: 0; top: 790px; width: 342px; height: 66px; }
  .banner--win .ribbon__text { left: 28px; top: 3px; font-size: 23px; line-height: 30px; }

  .form-panel { position: absolute; left: 0; top: 765px; width: 100%; height: 160px; background: var(--form-panel); }
  .field { position: absolute; text-align: center; font-size: 21px; letter-spacing: 3px; text-transform: uppercase; }
  .field__label { display: block; line-height: 30px; }
  .field__line { display: block; height: 2px; margin-top: 8px; }
  .form-panel .field { width: 392px; color: var(--label-dark); }
  .form-panel .field__line { background: var(--ink-dark); }

  .submit {
    position: absolute; text-align: center; font-weight: 700;
    font-size: 21px; letter-spacing: 4px; text-transform: uppercase;
  }
  .form-panel .submit { left: 517px; top: 80px; width: 393px; height: 52px; line-height: 52px; background: var(--ink-dark); color: var(--accent); }

  .footnote {
    position: absolute; left: 0; width: 100%; text-align: center;
    font-size: 16px; letter-spacing: 0.2px; text-transform: uppercase;
  }
  .banner--offer .footnote { top: 925px; height: 35px; line-height: 35px; background: var(--accent); color: var(--ink-dark); }
  .banner--win .footnote { top: 930px; color: var(--text-muted); }

  .win-form .field { width: 366px; left: 604px; color: var(--text-muted); }
  .win-form .field__line { background: var(--text-light); }
  .win-form .submit { left: 604px; top: 806px; width: 366px; height: 50px; line-height: 50px; background: var(--accent); color: var(--ink-dark); }
</style>
</head>
<body>

<section class="banner banner--offer">
  <div class="photo photo--diners" role="img" aria-label="Friends laughing together at a restaurant dinner table with bread, wine and salads"></div>
  <h1 class="headline">WANT A GREAT OFFER?</h1>
  <p class="subline">Subscribe to our newsletter and<br>receive a complimentary</p>
  <div class="ribbon">
    <svg width="437" height="77" viewBox="0 0 437 77">
      <polygon points="32,0 437,0 405,77 0,77" fill="var(--accent)"/>
      <polygon points="0,0 32,0 16,38" fill="#ffffff"/>
      <polygon points="405,77 437,77 421,38" fill="#ffffff"/>
    </svg>
    <p class="ribbon__text">$300 Restaurant<br>Certificate</p>
  </div>
  <form class="form-panel">
    <div class="field" style="left:52px; top:10px;"><span class="field__label">Name</span><span class="field__line"></span></div>
    <div class="field" style="left:517px; top:10px;"><span class="field__label">Email</span><span class="field__line"></span></div>
    <div class="field" style="left:52px; top:80px;"><span class="field__label">Phone</span><span class="field__line"></span></div>
    <div class="submit">Submit</div>
  </form>
  <p class="footnote">We will send an email and a text message with the offer and instructions on how to redeem.</p>
</section>

<section class="banner banner--win">
  <div class="photo photo--plating" role="img" aria-label="Chef's hands garnishing a plated seared meat dish with fresh herbs"></div>
  <div class="dark-panel" role="img" aria-label="Dark blurred restaurant plates in the background"></div>
  <h1 class="headline">ENTER TO WIN</h1>
  <p class="subline">Subscribe to our newsletter<br>to enter to win a</p>
  <div class="ribbon">
    <svg width="342" height="66" viewBox="0 0 342 66">
      <polygon points="0,0 342,0 315,66 0,66" fill="var(--accent)"/>
      <polygon points="315,66 342,66 330,34" fill="#ffffff"/>
    </svg>
    <p class="ribbon__text">$300 Restaurant<br>Certificate</p>
  </div>
  <form class="win-form">
    <div class="field" style="top:587px;"><span class="field__label">Name</span><span class="field__line"></span></div>
    <div class="field" style="top:658px;"><span class="field__label">Email</span><span class="field__line"></span></div>
    <div class="field" style="top:729px;"><span class="field__label">Phone</span><span class="field__line"></span></div>
    <div class="submit">Submit</div>
  </form>
  <p class="footnote">We will send an email and a text message with the offer and instructions on how to redeem.</p>
</section>

</body>
</html>
```